Website for software company "velora"

We need a website for our software company/startup named "velora". We are developing several products (currently 3 standard-software products) which are all in different sectors, but all our products are available for Laptops/PC/Mobile Phones/Tablets, ... We do also create custom software and support our customers with consulting to optimize their processes.
We already have a Logo which you can find in the attached files.
We are a young team of 4 members (two founders and 2 employees).

To get an idea of our products -> the first one is a planning software for healthcare organizations (eg. BlueHaven, firebrigade, pharmacy), the second one is a booking software for sport clubs and the third one is a competition software for sports hunting. You see very diverse. Include or ignore this info of our products as you like.

The design has to be a bootstrap 4 (or higher) design. We have licenced FontAwesome as iconset. Responsive design should come without saying.

• Starting page, product pages, news section, contact, team, services

```html
<!DOCTYPE html>
<html lang="en">
<head>
<meta charset="utf-8">
<title>velora – Software Company</title>
<link rel="stylesheet" href="https://fonts.googleapis.com/css2?family=Poppins:wght@400;500;600;700;800&display=swap">
<style>
:root{
  --orange:#f58634;
  --orange-deep:#f47a20;
  --navy:#141a4a;
  --hero:#10263a;
  --ink:#111111;
  --text:#333333;
  --muted:#666666;
  --card:#ececec;
  --white:#ffffff;
}
*{box-sizing:border-box;margin:0;padding:0}
html,body{width:1200px;height:4843px;overflow:hidden}
body{font-family:'Poppins',sans-serif;color:var(--text);background:var(--white);position:relative}
.abs{position:absolute}
a{color:inherit;text-decoration:none}

/* top bar */
.topbar{top:0;left:0;width:1200px;height:38px;background:var(--orange);color:#fff;font-size:12px}
.topbar .social{left:113px;top:10px;display:flex;gap:5px}
.topbar .social span{width:17px;height:17px;border-radius:50%;background:#fff;display:block}
.topbar .info{right:113px;top:11px;display:flex;gap:26px;font-weight:500}
.topbar .info svg{vertical-align:-2px;margin-right:5px}

/* nav */
.nav{top:38px;left:0;width:1200px;height:84px;background:#fff}
.brand{left:113px;top:20px;font-size:36px;font-weight:700;letter-spacing:1px;color:var(--ink);display:flex;align-items:center;gap:10px;text-transform:uppercase}
.brand i{width:14px;height:34px;background:var(--orange);display:block}
.menu{left:443px;top:24px;display:flex;gap:0;font-size:14px;font-weight:500;color:var(--ink)}
.menu a{padding:9px 20px;margin-right:26px}
.menu a.active{background:var(--orange);color:#fff;border-radius:2px}

/* hero */
.hero{top:122px;left:0;width:1200px;height:640px;background:linear-gradient(90deg,#0f2234 0%,#13324a 60%,#16304a 100%)}
.hero-photo{left:480px;top:0;width:720px;height:610px;background:linear-gradient(180deg,#2a3f55 0%,#22344a 50%,#1d3c6e 100%)}
.hero h1{left:113px;top:95px;font-size:47px;line-height:50px;font-weight:700;color:#fff}
.hero h1 span{color:var(--orange)}
.hero p{left:113px;top:262px;width:420px;font-size:13.5px;line-height:22px;color:#fff}
.btn{background:var(--orange);color:#fff;font-size:13px;font-weight:500;display:flex;align-items:center;justify-content:center;gap:12px;border-radius:2px}
.hero .btn{left:113px;top:386px;width:180px;height:42px}
.hero-curve{left:0;top:500px}

/* welcome */
.welcome h2{left:113px;top:852px;font-size:33px;font-weight:700;color:var(--ink)}
.welcome p{left:113px;top:902px;width:480px;font-size:13.5px;line-height:26.5px;color:#222}
.welcome .more{left:113px;top:1114px;font-size:13px;font-weight:700;letter-spacing:1.5px;color:var(--ink);display:flex;gap:14px;align-items:center}
.welcome-photo{left:679px;top:814px;width:406px;height:312px;background:linear-gradient(180deg,#dfe3e8 0%,#8c96a3 55%,#2d3540 100%)}

/* services */
.services{top:1235px;left:0;width:1200px;height:605px;background:var(--orange);color:#fff;text-align:center}
.services h2{left:0;width:1200px;top:86px;font-size:33px;font-weight:700}
.services .sub{left:0;width:1200px;top:124px;font-size:16px}
.services .lead{left:235px;width:730px;top:160px;font-size:13.5px;line-height:25px}
.svc{top:297px;width:250px}
.svc .ico{width:50px;height:50px;border-radius:6px;background:#fff;margin:0 auto;display:flex;align-items:center;justify-content:center}
.svc h3{font-size:16px;font-weight:600;margin-top:12px}
.svc p{font-size:12px;line-height:19.5px;margin-top:10px;padding:0 8px}

/* about */
.about h2{left:0;width:1200px;top:1936px;text-align:center;font-size:33px;font-weight:700;color:var(--ink)}
.about .lead{left:250px;width:700px;top:1986px;text-align:center;font-size:13.5px;line-height:25px;color:#222}
.founders-photo{left:335px;top:2105px;width:585px;height:330px;background:linear-gradient(180deg,#f4f4f4 0%,#2c3e6a 55%,#3a3f47 100%);border-radius:0 0 40px 40px}
.founders-word{left:470px;top:2398px;width:300px;text-align:center;font-size:34px;font-weight:800;color:#9a9a9a;letter-spacing:1px}
.tag{font-size:10.5px;line-height:14px;text-align:center}
.tag b{display:block;color:var(--orange);font-weight:400}
.tag span{color:var(--ink);letter-spacing:1px}

/* testimonials */
.testi{top:2529px;left:0;width:1200px;height:481px;background:var(--orange);color:#fff}
.testi h2{left:113px;top:200px;font-size:33px;font-weight:700}
.testi .sub{left:115px;top:247px;font-size:15px}
.testi .quote{left:566px;top:150px;width:470px;font-size:13.5px;line-height:25px}
.testi .avatar{left:566px;top:259px;width:48px;height:48px;border-radius:50%;background:linear-gradient(180deg,#e9e9e9,#9aa3ad);border:2px solid #fff}
.testi .who{left:566px;top:320px;font-size:14px;font-weight:600}
.testi .role{left:566px;top:341px;font-size:9.5px}
.testi .dots{left:566px;top:370px;display:flex;gap:4px}
.testi .dots i{width:7px;height:7px;border-radius:50%;background:#fff;display:block}
.testi .dots i:first-child{background:#222}

/* projects */
.projects h2{left:0;width:1200px;top:3082px;text-align:center;font-size:33px;font-weight:700;color:var(--ink)}
.proj{top:3168px;width:314px;height:265px;border-radius:8px;background:linear-gradient(135deg,#1c1c1c 0%,#2d2d2d 50%,#141414 100%);color:#fff}
.proj svg.icon{position:absolute;left:25px;top:115px}
.proj h3{position:absolute;left:25px;top:188px;width:230px;font-size:15px;font-weight:400;line-height:19px}
.proj .arrow{position:absolute;left:25px;top:224px}

/* team */
.team h2{left:0;width:1200px;top:3526px;text-align:center;font-size:33px;font-weight:700;color:var(--ink)}
.team .sub{left:0;width:1200px;top:3568px;text-align:center;font-size:16px;color:var(--ink)}
.member{top:3638px;width:222px;height:312px;background:var(--card);border:1px solid #e0e0e0}
.member .photo{width:100%;height:225px;background:linear-gradient(180deg,#f2f2f2 0%,#cfd3d8 45%,#2b3550 100%)}
.member h3{margin:32px 0 0 24px;font-size:14px;font-weight:400;color:#222}
.member p{margin:1px 0 0 24px;font-size:12px;color:#222}

/* let's talk */
.talk .kicker{left:113px;top:4122px;font-size:14px;color:var(--ink)}
.talk h2{left:113px;top:4140px;font-size:33px;font-weight:700;color:var(--ink)}
.talk p{left:113px;top:4198px;width:740px;font-size:13.5px;line-height:25px;color:#222}
.talk .btn{left:904px;top:4187px;width:183px;height:41px}

/* footer */
.footer{top:4310px;left:0;width:1200px;height:533px;background:var(--navy);color:#fff}
.footer .curve{left:0;top:0}
.footer .brand{left:113px;top:190px;color:#fff;font-size:44px;top:186px}
.footer .brand i{background:#fff;height:42px}
.fcol h4{font-size:16px;font-weight:500;color:var(--orange);position:relative;padding-top:14px}
.fcol h4::before{content:"";position:absolute;left:0;top:0;width:34px;height:4px;background:var(--orange)}
.vline{width:1px;background:#5b6094}
.vmark{width:4px;height:30px;background:var(--orange)}
.sitemap ul{list-style:none;margin-top:16px}
.sitemap li{font-size:13.5px;line-height:30.5px}
.sitemap li::before{content:"";display:inline-block;width:5px;height:5px;border-radius:50%;background:var(--orange);margin-right:9px;vertical-align:2px}
.contact .row{display:flex;gap:12px;margin-top:18px}
.contact .dot{width:24px;height:24px;border-radius:50%;background:var(--orange);display:flex;align-items:center;justify-content:center;flex:none;margin-top:5px}
.contact .row b{display:block;font-size:13px;font-weight:500;color:var(--orange);line-height:16px}
.contact .row span{font-size:13.5px;line-height:18px}
.news p{font-size:12px;line-height:17px;margin-top:16px;width:260px}
.news .field{margin-top:18px;width:262px;height:36px;background:#fff;border-radius:18px;display:flex;align-items:center;padding-left:18px;gap:8px;font-size:9px;color:#777;position:relative}
.news .field .send{position:absolute;right:0;top:0;width:58px;height:36px;border-radius:18px;background:var(--orange);display:flex;align-items:center;justify-content:center}
.news .circles{display:flex;gap:8px;margin-top:20px}
.news .circles i{width:29px;height:29px;border-radius:50%;background:#fff;display:block}
.footer .rule{left:113px;top:431px;width:974px;height:1px;background:#5b6094}
.footer .copy{left:0;width:1200px;top:462px;text-align:center;font-size:13.5px}
.footer .copy span{color:var(--orange)}
.totop{left:1040px;top:452px;width:45px;height:45px;background:#fff;display:flex;align-items:center;justify-content:center}
</style>
</head>
<body>

<header>
  <div class="abs topbar">
    <div class="abs social" aria-label="Social links"><span></span><span></span><span></span><span></span></div>
    <div class="abs info">
      <span><svg width="11" height="11" viewBox="0 0 24 24" fill="#fff"><path d="M6.6 10.8a15 15 0 006.6 6.6l2.2-2.2c.3-.3.7-.4 1-.2 1.1.4 2.3.6 3.6.6.6 0 1 .4 1 1V20c0 .6-.4 1-1 1C10.6 21 3 13.4 3 4c0-.6.4-1 1-1h3.5c.6 0 1 .4 1 1 0 1.3.2 2.5.6 3.6.1.3 0 .7-.2 1z"/></svg>+1-555-210-4471 3820</span>
      <span><svg width="10" height="12" viewBox="0 0 24 24" fill="#fff"><path d="M12 2a7 7 0 00-7 7c0 5 7 13 7 13s7-8 7-13a7 7 0 00-7-7zm0 9.5A2.5 2.5 0 1112 6a2.5 2.5 0 010 5.5z"/></svg>Linden Avenue Harbor, Canada</span>
      <span><svg width="11" height="11" viewBox="0 0 24 24" fill="#fff"><path d="M2 21l21-9L2 3v7l15 2-15 2z"/></svg>hello@velora-mail.com</span>
    </div>
  </div>
  <nav class="abs nav">
    <div class="abs brand"><i></i>velora</div>
    <div class="abs menu">
      <a class="active">Home</a><a>Product</a><a>News</a><a>Contact</a><a>Team</a><a>Services</a>
    </div>
  </nav>
</header>

<section class="abs hero">
  <div class="abs hero-photo" role="img" aria-label="Photo of the two founders in suits, arms crossed, smiling in an office"></div>
  <h1 class="abs">World Leading<br><span>Digital Marketing</span><br>Agency</h1>
  <p class="abs">Lorem ipsum dolor sit amet, consectetur adipiscing elit, sed do eiusmod tempor dolore magna aliqua. Quis ipsum suspendisse ultrices gravida. Risus commodo viverra maecenas accumsan lacus vel facilisis.</p>
  <a class="abs btn">Get Started Now <svg width="8" height="12" viewBox="0 0 8 12"><path d="M1 1l5 5-5 5" stroke="#fff" stroke-width="2" fill="none"/></svg></a>
  <svg class="abs hero-curve" width="1200" height="140" viewBox="0 0 1200 140">
    <path d="M0 45 C300 115 520 125 720 112 C900 100 1060 60 1200 30 L1200 140 L0 140Z" fill="#fff"/>
    <path d="M0 45 C300 115 520 125 720 112 C900 100 1060 60 1200 30" stroke="#f58634" stroke-width="9" fill="none"/>
  </svg>
  <svg class="abs" style="left:587px;top:492px" width="26" height="46" viewBox="0 0 26 46"><rect x="2" y="2" width="22" height="42" rx="11" stroke="#fff" stroke-width="2" fill="none"/><rect x="12" y="10" width="2" height="8" fill="#fff"/></svg>
</section>

<section class="welcome">
  <h2 class="abs">Welcome to velora</h2>
  <p class="abs">Lorem ipsum dolor sit amet, consectetur adipiscing elit, sed do eiusmod tempor dolore magna aliqua. Quis ipsum suspendisse ultrices gravida. Risus commodo viverra maecenas accumsan lacus vel facilisis.Lorem ipsum dolor sit amet, consectetur adipiscing elit, sed do eiusmod tempor dolore magna aliqua. Quis ipsum suspendisse ultrices gravida. Risus commodo viverra maecenas accumsan lacus vel facilisis.</p>
  <a class="abs more">LEARN MORE <svg width="24" height="14" viewBox="0 0 24 14"><path d="M2 2l5 5-5 5M10 2l5 5-5 5M18 2l5 5-5 5" stroke="#111" stroke-width="2.4" fill="none"/></svg></a>
  <div class="abs welcome-photo" role="img" aria-label="Photo of the velora team standing together in business attire"></div>
</section>

<section class="abs services">
  <h2 class="abs">Our Services</h2>
  <div class="abs sub">With all the Features You Need</div>
  <p class="abs lead">Lorem ipsum dolor sit amet, consectetur adipiscing elit, sed do eiusmod tempor dolore magna aliqua. Quis ipsum suspendisse ultrices gravida. Risus commodo viverra maecenas accumsan lacus vel facilisis.Lorem ipsum dolor sit amet, consectetur</p>
  <div class="abs svc" style="left:195px">
    <div class="ico"><svg width="28" height="28" viewBox="0 0 28 28" fill="none" stroke="#f58634" stroke-width="2"><circle cx="14" cy="15" r="5"/><path d="M14 3v4M4 15h4M20 15h4M7 8l3 3M21 8l-3 3"/></svg></div>
    <h3>Good Performance</h3>
    <p>Lorem ipsum dolor sit amet, consectetur adipiscing elit, sed do eiusmod tempor dolore magna aliqua. Quis ipsum suspendisse ultrices gravida.</p>
  </div>
  <div class="abs svc" style="left:486px">
    <div class="ico"><svg width="28" height="28" viewBox="0 0 28 28" fill="none" stroke="#f58634" stroke-width="2"><path d="M14 3l9 4v6c0 6-4 10-9 12-5-2-9-6-9-12V7z"/><path d="M10 14l3 3 5-6"/></svg></div>
    <h3>Highly Secure</h3>
    <p>Appropriately grow competitive leadership rother than strategic technically sound processes without state.</p>
  </div>
  <div class="abs svc" style="left:774px">
    <div class="ico"><svg width="28" height="28" viewBox="0 0 28 28" fill="none" stroke="#f58634" stroke-width="2"><circle cx="14" cy="15" r="9"/><circle cx="14" cy="15" r="4"/><path d="M10 4h8"/></svg></div>
    <h3>Fast Development</h3>
    <p>Lorem ipsum dolor sit amet, consectetur adipiscing elit, sed do eiusmod tempor dolore magna aliqua. Quis ipsum suspendisse ultrices gravida.</p>
  </div>
</section>

<section class="about">
  <h2 class="abs">About Us</h2>
  <p class="abs lead">Lorem ipsum dolor sit amet, consectetur adipiscing elit, sed do eiusmod tempor dolore magna aliqua. Quis ipsum suspendisse ultrices gravida. Risus commodo viverra maecenas accumsan lacus vel facilisis.Lorem ipsum dolor sit amet, consectetur</p>
  <div class="abs founders-photo" role="img" aria-label="Photo of the two founders standing on either side of the company name"></div>
  <div class="abs" style="left:545px;top:2245px;width:150px;text-align:center;font-size:30px;font-weight:700;color:var(--orange)">velora</div>
  <div class="abs founders-word">FOUNDERS</div>
  <div class="abs tag" style="left:240px;top:2197px"><b>LUCAS BRENNER</b><span>( FOUNDER )</span></div>
  <svg class="abs" style="left:285px;top:2225px" width="60" height="40" viewBox="0 0 60 40"><path d="M55 22 C45 38 15 38 6 10" stroke="#f58634" stroke-width="2.5" fill="none"/><path d="M1 16l5-8 5 7" stroke="#f58634" stroke-width="2.5" fill="none"/></svg>
  <div class="abs tag" style="left:890px;top:2152px"><b>MARC HOLLAND</b><span>( FOUNDER )</span></div>
  <svg class="abs" style="left:880px;top:2183px" width="60" height="46" viewBox="0 0 60 46"><path d="M50 4 C60 30 40 42 8 40" stroke="#f58634" stroke-width="2.5" fill="none"/><path d="M14 34l-7 6 7 5" stroke="#f58634" stroke-width="2.5" fill="none"/></svg>
</section>

<section class="abs testi">
  <h2 class="abs">Testimonials</h2>
  <div class="abs sub">Our Customer Valuable Feedback</div>
  <svg class="abs" style="left:566px;top:106px" width="38" height="28" viewBox="0 0 38 28" fill="#fff"><path d="M0 0h16v14l-6 14H4l4-12H0zM22 0h16v14l-6 14h-6l4-12h-8z"/></svg>
  <p class="abs quote">Lorem ipsum dolor sit amet, consectetur adipiscing elit, sed do eiusmod tempor dolore magna aliqua. Quis ipsum suspendisse ultrices gravida. Risus commodo viverra maecenas accumsan lacus vel facilisis.Lorem ipsum dolor sit amet, consectetur</p>
  <svg class="abs" style="left:966px;top:250px" width="62" height="42" viewBox="0 0 62 42" fill="#f9a866"><path d="M0 0h26v20l-8 22H9l6-18H0zM36 0h26v20l-8 22h-9l6-18H36z"/></svg>
  <div class="abs avatar" role="img" aria-label="Portrait of the reviewer"></div>
  <div class="abs who">Lucas Brenner</div>
  <div class="abs role">(Marketing company XYZ Company)</div>
  <div class="abs dots"><i></i><i></i><i></i><i></i></div>
</section>

<section class="projects">
  <h2 class="abs">Projects We Worked On</h2>
  <article class="abs proj" style="left:113px" role="group" aria-label="Healthcare organizations project">
    <svg class="icon" width="70" height="60" viewBox="0 0 70 60" fill="none" stroke="#f58634" stroke-width="2.5"><rect x="3" y="3" width="64" height="42" rx="2"/><path d="M25 57h20M35 45v12"/><circle cx="35" cy="24" r="9"/><path d="M35 10v5M35 33v5M21 24h5M44 24h5"/></svg>
    <h3>Healthcare organizations</h3>
    <svg class="arrow" width="36" height="14" viewBox="0 0 36 14"><path d="M0 7h33M27 1l6 6-6 6" stroke="#f58634" stroke-width="2" fill="none"/></svg>
  </article>
  <article class="abs proj" style="left:444px" role="group" aria-label="Software for sport clubs project">
    <svg class="icon" width="70" height="60" viewBox="0 0 70 60" fill="none" stroke="#f58634" stroke-width="2.5"><rect x="3" y="3" width="64" height="42" rx="2"/><path d="M25 57h20M35 45v12"/><path d="M24 36V26M33 36V20M42 36V15M51 36V24"/><circle cx="15" cy="16" r="6"/></svg>
    <h3>Software for sport clubs</h3>
    <svg class="arrow" width="36" height="14" viewBox="0 0 36 14"><path d="M0 7h33M27 1l6 6-6 6" stroke="#f58634" stroke-width="2" fill="none"/></svg>
  </article>
  <article class="abs proj" style="left:773px" role="group" aria-label="Competition software project">
    <svg class="icon" width="70" height="60" viewBox="0 0 70 60" fill="none" stroke="#f58634" stroke-width="2.5"><rect x="3" y="3" width="64" height="50" rx="2"/><path d="M3 13h64"/><rect x="14" y="22" width="42" height="22"/><path d="M30 28l-5 5 5 5M40 28l5 5-5 5"/></svg>
    <h3>Competition software for sports hunting</h3>
    <svg class="arrow" width="36" height="14" viewBox="0 0 36 14" style="top:244px"><path d="M0 7h33M27 1l6 6-6 6" stroke="#f58634" stroke-width="2" fill="none"/></svg>
  </article>
</section>

<section class="team">
  <h2 class="abs">Our Team</h2>
  <div class="abs sub">We Help To Achieve Your Business Goal</div>
  <article class="abs member" style="left:113px"><div class="photo" role="img" aria-label="Portrait of a founder in a navy suit"></div><h3>Marc Holland</h3><p>CEO &amp; Founder</p></article>
  <article class="abs member" style="left:359px"><div class="photo" role="img" aria-label="Portrait of a founder in a grey suit"></div><h3>Lucas Brenner</h3><p>CEO &amp; Founder</p></article>
  <article class="abs member" style="left:607px"><div class="photo" role="img" aria-label="Portrait of an employee in a dark blazer"></div><h3>Nina Caldwell</h3><p>Employee</p></article>
  <article class="abs member" style="left:863px"><div class="photo" role="img" aria-label="Portrait of an employee with glasses in a grey blazer"></div><h3>Daniel Morrow</h3><p>Employee</p></article>
</section>

<section class="talk">
  <div class="abs kicker">Let's Talk</div>
  <h2 class="abs">Get Started A Project?</h2>
  <p class="abs">Lorem ipsum dolor sit amet, consectetur adipiscing elit, sed do eiusmod tempor dolore magna aliqua. Quis ipsum suspendisse ultrices gravida. Risus commodo viverra maecenas accumsan lacus vel facilisis.Lorem ipsum dolor sit amet, consectetur</p>
  <a class="abs btn">Get Started Now <svg width="8" height="12" viewBox="0 0 8 12"><path d="M1 1l5 5-5 5" stroke="#fff" stroke-width="2" fill="none"/></svg></a>
</section>

<footer class="abs footer">
  <svg class="abs curve" width="1200" height="80" viewBox="0 0 1200 80"><path d="M0 0 L1200 0 L1200 14 C900 72 300 72 0 14Z" fill="#fff"/></svg>
  <div class="abs brand"><i></i>velora</div>

  <div class="abs vline" style="left:352px;top:162px;height:256px"></div>
  <div class="abs vmark" style="left:350px;top:260px"></div>
  <div class="abs vline" style="left:521px;top:162px;height:256px"></div>
  <div class="abs vmark" style="left:519px;top:260px"></div>
  <div class="abs vline" style="left:791px;top:162px;height:256px"></div>
  <div class="abs vmark" style="left:789px;top:260px"></div>

  <div class="abs fcol sitemap" style="left:402px;top:164px">
    <h4>Sitemap</h4>
    <ul><li>Home</li><li>Product</li><li>News</li><li>Contact</li><li>Team</li><li>Services</li></ul>
  </div>

  <div class="abs fcol contact" style="left:556px;top:162px">
    <h4>Contact Us</h4>
    <div class="row"><div class="dot"><svg width="10" height="12" viewBox="0 0 24 24" fill="#fff"><path d="M12 2a7 7 0 00-7 7c0 5 7 13 7 13s7-8 7-13a7 7 0 00-7-7zm0 9.5A2.5 2.5 0 1112 6a2.5 2.5 0 010 5.5z"/></svg></div><div><b>Address</b><span>Oakridge, Tx 70411</span></div></div>
    <div class="row"><div class="dot"><svg width="11" height="11" viewBox="0 0 24 24" fill="#fff"><path d="M2 21l21-9L2 3v7l15 2-15 2z"/></svg></div><div><b>Email</b><span>support@velora-mail.com</span></div></div>
    <div class="row"><div class="dot"><svg width="11" height="11" viewBox="0 0 24 24" fill="#fff"><path d="M6.6 10.8a15 15 0 006.6 6.6l2.2-2.2c.3-.3.7-.4 1-.2 1.1.4 2.3.6 3.6.6.6 0 1 .4 1 1V20c0 .6-.4 1-1 1C10.6 21 3 13.4 3 4c0-.6.4-1 1-1h3.5c.6 0 1 .4 1 1 0 1.3.2 2.5.6 3.6.1.3 0 .7-.2 1z"/></svg></div><div><b>Contact</b><span>+44-20-5550-1186</span></div></div>
  </div>

  <div class="abs fcol news" style="left:823px;top:164px">
    <h4>Subscribe to our Newsletter</h4>
    <p>When an unknown printer took a galley of type and scrambled.</p>
    <div class="field"><svg width="12" height="9" viewBox="0 0 12 9" fill="none" stroke="#777"><rect x=".5" y=".5" width="11" height="8"/><path d="M.5 .5l5.5 4 5.5-4"/></svg>Email Address<span class="send"><svg width="16" height="16" viewBox="0 0 24 24" fill="#fff"><path d="M2 21l21-9L2 3v7l15 2-15 2z"/></svg></span></div>
    <div class="circles" aria-label="Social links"><i></i><i></i><i></i><i></i></div>
  </div>

  <div class="abs rule"></div>
  <div class="abs copy">Copyright © 2022 <span>velora</span> . All rights reserved.</div>
  <a class="abs totop" aria-label="Back to top"><svg width="28" height="16" viewBox="0 0 28 16"><path d="M2 14L14 3l12 11" stroke="#141a4a" stroke-width="1.5" fill="none"/></svg></a>
</footer>

</body>
</html>
```